Brightfen Business Card Redesign & Logo Update

We need to update our business cards to something more modern and fresh. Brightfen can provide the current color schemes and old design examples, but welcome creativity in helping us with this redesign. PLEASE NOTE that we no longer utilize the "tree" and/or "leaf" imagery in our branding. If able would apprecaite an update on the quality of our "words only" logo in Ai. / PNG formats too.

Target Market(s)

Investors, landowners, corporate partners, contractors

Industry/Entity Type

Environmental Restoration & Conservation

Contact Information for Business Card

Logo, persons name, title, mailing address, phone and email, website url

Font styles to use
Other font styles liked:
• Merriweather

Requirements
Nice to have
• Logo, persons name, title, mailing address, phone and email, website url, but open to ideams
Should not have
• No all back backgrounds

```html
<!DOCTYPE html>
<html lang="en">
<head>
<meta charset="utf-8">
<title>Brightfen Business Card</title>
<link rel="stylesheet" href="https://fonts.googleapis.com/css2?family=Merriweather:wght@400;700&display=swap">
<style>
  :root {
    --backdrop: #e4e5e7;
    --paper: #ffffff;
    --brand-green: #16803f;
    --brand-orange: #ee7d22;
    --ink: #1d1d1b;
    --card-shadow: 0 10px 28px rgba(0,0,0,0.18);
  }
  * { margin: 0; padding: 0; box-sizing: border-box; }
  html, body { width: 1200px; height: 1059px; overflow: hidden; }
  body {
    background: var(--backdrop);
    display: flex;
    flex-direction: column;
    align-items: center;
    justify-content: center;
    gap: 60px;
    font-family: "Merriweather", Georgia, serif;
    color: var(--ink);
  }
  .card {
    position: relative;
    width: 700px;
    height: 400px;
    background: var(--paper);
    box-shadow: var(--card-shadow);
    overflow: hidden;
  }
  .wordmark {
    font-family: "Merriweather", Georgia, serif;
    font-weight: 700;
    color: var(--brand-green);
    line-height: 1;
    white-space: nowrap;
  }
  /* Front */
  .card-front { display: flex; align-items: center; justify-content: center; }
  .card-front .wordmark { font-size: 76px; }
  /* Back */
  .card-back .wordmark { position: absolute; left: 40px; top: 96px; font-size: 54px; }
  .person { position: absolute; right: 40px; top: 44px; text-align: right; }
  .person-name {
    font-weight: 700; font-size: 21px; color: var(--brand-orange); letter-spacing: 0.5px;
  }
  .person-name .surname { color: var(--brand-green); }
  .person-title { font-size: 15px; margin-top: 2px; }
  .divider {
    position: absolute; left: 40px; top: 205px; width: 440px; height: 2px;
    background: var(--brand-orange);
  }
  .contacts { position: absolute; left: 40px; top: 222px; list-style: none; }
  .contacts li { display: flex; align-items: center; gap: 10px; font-size: 17px; line-height: 1.55; }
  .contacts svg { width: 14px; height: 14px; fill: var(--brand-orange); flex: none; }
  .address {
    position: absolute; right: 40px; top: 148px; text-align: right;
    font-size: 15px; line-height: 1.6; font-style: normal;
  }
  .bands { position: absolute; left: 0; top: 0; width: 700px; height: 400px; }
</style>
</head>
<body>
  <section class="card card-front">
    <div class="wordmark">Brightfen</div>
  </section>

  <section class="card card-back">
    <svg class="bands" viewBox="0 0 700 400" aria-hidden="true">
      <polygon points="545,240 700,240 700,400 505,400" fill="var(--brand-green)"/>
      <polygon points="0,342 520,342 518,350 0,350" fill="var(--brand-green)"/>
      <polygon points="0,365 510,365 500,400 0,400" fill="var(--brand-orange)"/>
    </svg>

    <div class="wordmark">Brightfen</div>

    <div class="person">
      <div class="person-name">NOLAN <span class="surname">REYES</span></div>
      <div class="person-title">Founder</div>
    </div>

    <div class="divider"></div>

    <ul class="contacts">
      <li><svg viewBox="0 0 24 24"><path d="M6.6 10.8a15.1 15.1 0 0 0 6.6 6.6l2.2-2.2a1 1 0 0 1 1-.25 11.4 11.4 0 0 0 3.6.57 1 1 0 0 1 1 1V20a1 1 0 0 1-1 1A17 17 0 0 1 3 4a1 1 0 0 1 1-1h3.5a1 1 0 0 1 1 1c0 1.25.2 2.45.57 3.57a1 1 0 0 1-.25 1z"/></svg>(555) 214-3080</li>
      <li><svg viewBox="0 0 24 24"><path d="M2 5h20v14H2z M2 5l10 8 10-8"/></svg>hello@brightfenmail.com</li>
      <li><svg viewBox="0 0 24 24"><circle cx="12" cy="12" r="10"/></svg>www.brightfen.com</li>
    </ul>

    <address class="address">
      48 Marsh Lane Office<br>Reed Rd, PO 7182, Fenwick
    </address>
  </section>
</body>
</html>
```